Web design for Crowdfunding site HopeWingsRally.com

We need a web design for christian crowdfunding website. Here is the challenge: We need responsive layout that is targeted first in iPad size of screen. It should also scale somehow down to iPhone size of screens. Web layout can be about the same size as iPad screen.

Screens should work so that main page scrolls not but only certain part of the screen scrolls and always one "page" at time. We can implement these "scrolls" then later with javascript but now we need only design. The challenge is to create this kind of hybrid website / app look.

Target is at first to raise funds to orphan people needing about $40 per month for their living and education. There is always some organization which takes care of these kids. Later there will be other christian missions included. At first we are looking to find monthly supporters.

You can be as creative as you want :) As you see from the look and feel sector, I am not looking any same traditional look which many "help kids" sites have. I am looking to reach now younger generation and therefore iPad and mobile are the main screen sizes.

Inspirational designs:
- https://example-gallery.test/profiles/studiofernlake/designs/482716?from=%2Fbrowse%2Fxhr%2Fdesigns%3Fcategory%3Dmobile-app-design
- http://www.artpoolhub.test/design/8261047 Clear, simple visuals
- http://www.artpoolhub.test/design/7394215 Header
- http://www.artpoolhub.test/design/6048392 Contrast in the colors, i think is powerfull

Some terms could be: Kids play, kids are learning (in the school). No static posture but living like kids are. I wonder also how we could also add little bit gaming style even though the question is of reali life of real people. Giving should be rewarding.

Target Market(s)

People who want help other people.

Industry/Entity Type

Christian

Number of Pages Required

4 page

Requirements
Must have
• Homepage. Mission page (In my wireframes it was one kid).
Nice to have
• Other pages and some idea how to scroll. 4 pages is no must. If you feel easy, please give first some draft and I give comments on that.

```html
<!DOCTYPE html>
<html lang="en">
<head>
<meta charset="utf-8">
<title>HopeWingsRally</title>
<link rel="stylesheet" href="https://fonts.googleapis.com/css2?family=Montserrat:wght@400;500;600&family=Open+Sans:wght@400&display=swap">
<style>
:root{
  --black:#000;
  --white:#fff;
  --sun:#f6c400;
  --sun-deep:#f0a800;
  --amber:#e88a00;
  --footer:#1c1606;
  --ink:#0a0a0a;
}
*{box-sizing:border-box;margin:0;padding:0}
html,body{width:1200px;height:794px;overflow:hidden;background:var(--black)}
body{font-family:"Montserrat",Arial,sans-serif;position:relative}
.site-header{position:absolute;left:0;top:0;width:1200px;height:91px;background:var(--black);color:var(--white)}
.missions-menu{position:absolute;left:131px;top:38px;display:flex;align-items:center;gap:8px;font-size:14px;font-weight:500;letter-spacing:.3px}
.missions-menu svg{display:block}
.brand{position:absolute;left:0;width:100%;top:29px;text-align:center;font-size:26px;font-weight:500;letter-spacing:.6px}
.account-actions{position:absolute;right:141px;top:31px;display:flex;gap:17px}
.account-actions a{display:block;height:33px;padding:0 19px;line-height:30px;border:2px solid var(--white);color:var(--white);text-decoration:none;font-size:14px;font-weight:500}
.hero{position:absolute;left:0;top:91px;width:1200px;height:653px;overflow:hidden}
.hero-photo{position:absolute;inset:0;background:
  radial-gradient(ellipse 380px 520px at 920px 420px,var(--amber) 0%,rgba(240,168,0,.55) 45%,rgba(246,196,0,0) 75%),
  linear-gradient(90deg,var(--sun) 0%,var(--sun) 55%,var(--sun-deep) 100%)}
.hero-copy{position:absolute;left:0;width:100%;top:210px;text-align:center}
.hero-title{font-size:50px;font-weight:500;color:var(--ink);letter-spacing:-.3px;line-height:1.2}
.hero-lead{margin-top:8px;font-size:31px;font-weight:500;color:var(--white);line-height:1.4}
.site-footer{position:absolute;left:0;top:744px;width:1200px;height:50px;background:var(--footer);color:var(--white);text-align:center;font-family:"Open Sans",Arial,sans-serif;font-size:13px;line-height:44px}
</style>
</head>
<body>
<header class="site-header">
  <nav class="missions-menu">
    <svg width="30" height="16" viewBox="0 0 30 16" aria-hidden="true"><rect y="0" width="30" height="3" rx="1.5" fill="#fff"/><rect y="6.5" width="30" height="3" rx="1.5" fill="#fff"/><rect y="13" width="30" height="3" rx="1.5" fill="#fff"/></svg>
    <span>SEE THE MISSIONS</span>
    <svg width="17" height="17" viewBox="0 0 17 17" aria-hidden="true"><circle cx="7" cy="7" r="5" fill="none" stroke="#666" stroke-width="2.4"/><line x1="10.5" y1="10.5" x2="15.5" y2="15.5" stroke="#666" stroke-width="3" stroke-linecap="round"/></svg>
  </nav>
  <div class="brand">HOPEWINGSRALLY</div>
  <div class="account-actions">
    <a href="#">LOGIN</a>
    <a href="#">SIGN UP</a>
  </div>
</header>
<main class="hero">
  <div class="hero-photo" role="img" aria-label="Young woman smiling while reading on a sofa, tinted in warm yellow"></div>
  <div class="hero-copy">
    <h1 class="hero-title">She has a name. He has dreams.</h1>
    <p class="hero-lead">She hopes she would have a future. He is like your".<br>"I USD a month will help her and him”</p>
  </div>
</main>
<footer class="site-footer">© 2016 Company Name&nbsp; All right reserved&nbsp; Term of Use</footer>
</body>
</html>
```